Counselling business requires poster

I require a poster to promote my counselling and coaching business I will be placing these in doctors surgery's and clinics etc.
This business is centred around helping people work through emotional issues. We provided one on one sessions which help enhance peoples lives by assisting them in overcoming their fears, obsessions, insecurities etc.

We offer support in a broad range of areas:

- Eating disorders & weight managment
- Depression
- Marriage and relationship issues
- Anxiety
- Victims of physical, verbal and/or social abuse

We want our poster to be representative of the positive, warm and welcoming atmosphere we provide.

Our motto, 'One step at a time', is symbolic of our approach and how we help our clients to tackle their problems bit by bit.

The flyer I have uploaded is just some information on what we offer

Thankyou for your designs I am taking them into consideration and will inform you of any decision.

Weight

```html
<!DOCTYPE html>
<html lang="en">
<head>
<meta charset="utf-8">
<title>One Step at a Time – Pathways Counseling</title>
<link rel="stylesheet" href="https://fonts.googleapis.com/css2?family=Oswald:wght@600;700&family=Source+Sans+3:wght@400;700&display=swap">
<style>
  :root {
    --navy: #221c44;
    --amber: #f6a41f;
    --amber-text: #f3a93a;
    --white: #ffffff;
    --ink: #2a2550;
    --photo-light: #e8b53a;
    --photo-mid: #b07a16;
    --photo-dark: #4a3208;
  }
  * { margin: 0; padding: 0; box-sizing: border-box; }
  html, body { width: 849px; height: 1200px; overflow: hidden; background: var(--navy); }
  .poster {
    position: relative;
    width: 849px;
    height: 1200px;
    background: var(--navy);
    font-family: "Source Sans 3", "Myriad Pro", Arial, sans-serif;
    overflow: hidden;
  }
  .hero-photo {
    position: absolute;
    left: 0; top: 0;
    width: 849px; height: 537px;
    background:
      radial-gradient(ellipse 420px 260px at 520px 200px, rgba(255,226,120,0.75), rgba(255,226,120,0) 70%),
      linear-gradient(180deg, var(--photo-mid) 0%, var(--photo-light) 45%, var(--photo-mid) 75%, var(--photo-dark) 100%);
  }
  .motto {
    position: absolute;
    left: 395px;
    top: 88px;
    font-family: "Oswald", "Arial Narrow", sans-serif;
    font-weight: 700;
    color: var(--white);
    text-transform: uppercase;
    text-shadow: 3px 3px 4px rgba(0,0,0,0.55);
    transform-origin: left top;
  }
  .motto-line { display: block; line-height: 0.86; letter-spacing: -2px; transform-origin: left top; }
  .motto-one  { font-size: 165px; transform: scaleX(0.78); }
  .motto-step { font-size: 165px; transform: scaleX(0.70); margin-top: -4px; }
  .motto-time { font-size: 72px;  transform: scaleX(0.70); margin-top: 4px; letter-spacing: -1px; }

  .content {
    position: absolute;
    left: 248px;
    top: 576px;
    width: 362px;
    color: var(--amber-text);
  }
  .content-heading {
    font-weight: 700;
    font-size: 20px;
    color: var(--amber);
    margin-left: 2px;
    margin-bottom: 26px;
  }
  .content p, .service-list {
    font-size: 13.4px;
    line-height: 17px;
    margin-bottom: 17px;
  }
  .service-list { list-style: none; }

  .footer-card {
    position: absolute;
    left: 241px;
    top: 1067px;
    width: 378px;
    height: 133px;
    background: var(--white);
    text-align: center;
  }
  .brand {
    display: flex;
    align-items: center;
    justify-content: center;
    gap: 8px;
    margin-top: 32px;
    font-family: "Oswald", "Arial Narrow", sans-serif;
    font-weight: 600;
    font-size: 24px;
    letter-spacing: 0.5px;
    color: var(--ink);
  }
  .brand-dot { width: 30px; height: 30px; border-radius: 50%; background: var(--amber); }
  .contact {
    font-family: "Oswald", "Arial Narrow", sans-serif;
    font-weight: 600;
    font-size: 10.5px;
    color: var(--ink);
    line-height: 15px;
    margin-top: 8px;
  }
  .contact-web { margin-left: 26px; }
</style>
</head>
<body>
<main class="poster">
  <div class="hero-photo" role="img" aria-label="Photo of a person walking a small dog along a sunlit autumn forest path"></div>

  <h1 class="motto">
    <span class="motto-line motto-one">One</span>
    <span class="motto-line motto-step">Step</span>
    <span class="motto-line motto-time">At a time</span>
  </h1>

  <section class="content">
    <h2 class="content-heading">Professional and confidential service</h2>
    <p>Lorem ipsum dolor sit amet, consectetur adipiscing elit. Vivamus eleifend consectetur mi, quis consequat tellus euismod sit amet.</p>
    <p>Proin ac quam in urna consectetur feugiat. Nullam vulputate lobortis lacus, a dignissim nisi consequat nec.</p>
    <p>We offer support in a broad range of areas:</p>
    <ul class="service-list">
      <li>- Eating disorders &amp; weight managment</li>
      <li>- Depression</li>
      <li>- Marriage and relationship issues</li>
      <li>- Anxiety</li>
    </ul>
    <p>Sed sollicitudin pellentesque magna, a pulvinar ipsum eleifend vel. Duis porta sem eget nunc pretium tincidunt. Class aptent taciti sociosqu ad litora torquent per conubia nostra, per inceptos himenaeos. Duis tempor ante non laoreet sodales. Nunc euismod lorem massa. Sed at sapien non arcu tristique ultrices id at elit.</p>
    <p>&nbsp;Donec porta interdum dolor sit amet aliquet. Suspendisse bibendum rutrum diam non dignissim. Curabitur ac ullam-</p>
  </section>

  <footer class="footer-card">
    <div class="brand"><span class="brand-dot"></span><span class="brand-name">PATHWAYS COUNSELING</span></div>
    <div class="contact">
      <div class="contact-address">5678 Meadowbrook Lane, Riverton, Oregon 97321</div>
      <div class="contact-line"><span class="contact-phone">Phone: (555) 012.3344</span><span class="contact-web">www.pathwayscounseling.com</span></div>
    </div>
  </footer>
</main>
</body>
</html>
```